Building company buisness cards

We are looking for a sharp modern new look for our business cards.
We are a New Zealand based company that specialises in house and land packages.
We have attached a photo of the current logo and would like to see if it can be improved somehow if needed.
We are open to any colours but we have chosen green at this stage.
Feel free to change the font and make the logo smarter looking.
Play with the colours and see what looks best.

We want a card that looks so good know one will want to throw it away!

Target Market(s)

Home buyers

Industry/Entity Type

Building

Contact Information for Business Card

Derek Tolvane
0217394062
dtolvane@quillmarkhomesteads.co.nz
quillmarkhomesteads.co.nz

Font styles to use
Serif
Sans Serif

Colors

Designer to choose colors to be used in the design.

Requirements
Must have
• Logo and company name on one side, details on the other side
Nice to have
• Color codes for the original green are HEX #4a8028, RGB(74,128,40), CMYK(42,0,69,50)
• Round corners, Raised and/or spot UV

```html
<!DOCTYPE html>
<html lang="en">
<head>
<meta charset="utf-8">
<title>Quillmark Homesteads – Business Cards</title>
<link rel="stylesheet" href="https://fonts.googleapis.com/css2?family=Arimo:wght@700&family=Source+Sans+3:wght@400&display=swap">
<style>
  :root {
    --brand-green: #4a8028;
    --card-grey: #6a6a6a;
    --band-grey: #6d6d6d;
    --stage: #c9cacc;
    --paper: #ffffff;
    --ink: #222222;
  }
  * { margin: 0; padding: 0; box-sizing: border-box; }
  html, body { width: 1200px; height: 1015px; overflow: hidden; }
  body { background: var(--stage); position: relative; font-family: "Source Sans 3", sans-serif; }

  .card {
    position: absolute;
    width: 686px; height: 393px;
    border-radius: 33px;
    overflow: hidden;
    box-shadow: 0 3px 8px rgba(0,0,0,0.25);
  }
  .card--front { left: 425px; top: 73px; background: var(--paper); }
  .card--back  { left: 97px;  top: 524px; background: var(--card-grey); }

  .brand-mark {
    position: absolute; left: 50%;
    border-radius: 50%;
    transform: translateX(-50%);
  }
  .card--front .brand-mark { top: 30px; width: 52px; height: 52px; background: var(--brand-green); }
  .card--back  .brand-mark { top: 76px; width: 70px; height: 70px; background: var(--paper); }

  .brand-name {
    position: absolute; left: 0; width: 100%;
    text-align: center;
    font-family: "Arimo", sans-serif; font-weight: 700;
    line-height: 1; white-space: nowrap;
  }
  .card--front .brand-name { top: 113px; font-size: 32px; color: var(--brand-green); }
  .card--back  .brand-name { top: 190px; font-size: 42px; color: var(--paper); }

  .rule { position: absolute; height: 2px; }
  .card--front .rule { left: 273px; width: 120px; top: 174px; background: var(--brand-green); }
  .card--back .rule { left: 249px; width: 162px; top: 275px; background: var(--paper); }

  .person-name {
    position: absolute; left: 0; width: 100%; top: 195px;
    text-align: center;
    font-family: "Arimo", sans-serif; font-weight: 700;
    font-size: 26px; line-height: 1.2; color: var(--brand-green);
  }

  .contact { position: absolute; left: 0; top: 0; width: 100%; color: var(--ink); font-size: 17px; line-height: 1; }
  .contact li { list-style: none; position: absolute; left: 0; width: 100%; display: flex; justify-content: center; align-items: center; gap: 7px; }
  .contact .phone { top: 245px; }
  .contact .email { top: 274px; font-size: 16px; letter-spacing: -0.2px; }
  .contact .web   { top: 303px; }
  .contact svg { width: 15px; height: 15px; flex: none; }

  .waves { position: absolute; left: 0; bottom: 0; width: 686px; height: 393px; }

  .back-web {
    position: absolute; left: 0; width: 100%; top: 347px;
    text-align: center; color: var(--paper);
    font-size: 17px; letter-spacing: 2.6px;
  }
</style>
</head>
<body>

<section class="card card--front" aria-label="Business card front">
  <span class="brand-mark" aria-hidden="true"></span>
  <div class="brand-name">Quillmark Homesteads</div>
  <div class="rule"></div>
  <h1 class="person-name">Derek Tolvane</h1>
  <ul class="contact">
    <li class="phone">
      <svg viewBox="0 0 16 16" aria-hidden="true"><circle cx="8" cy="8" r="7" fill="none" stroke="var(--brand-green)" stroke-width="1.3"/><path d="M6 4.5c-1 1-1 3.5.6 5.4 1.6 1.9 3.6 2.3 4.4 1.4l-1.3-1.5-1 .6C7.6 9.8 6.9 8.8 6.7 7.7l.9-.8z" fill="var(--brand-green)"/></svg>
      0217394062
    </li>
    <li class="email">
      <svg viewBox="0 0 16 16" aria-hidden="true"><path d="M1 6.5 8 2l7 4.5V14H1z" fill="var(--brand-green)"/><path d="M1 6.5 8 11l7-4.5" fill="none" stroke="#fff" stroke-width="1.2"/><rect x="5" y="5.5" width="6" height="1" fill="#fff"/></svg>
      dtolvane@quillmarkhomesteads.co.nz
    </li>
    <li class="web">
      <svg viewBox="0 0 16 16" aria-hidden="true" fill="none" stroke="var(--brand-green)" stroke-width="1.1"><circle cx="8" cy="8" r="6.8"/><ellipse cx="8" cy="8" rx="3" ry="6.8"/><path d="M1.2 8h13.6M2.3 4.5h11.4M2.3 11.5h11.4"/></svg>
      www.quillmarkhomesteads.co.nz
    </li>
  </ul>
  <svg class="waves" viewBox="0 0 686 393" aria-hidden="true">
    <path d="M0 336 C120 318 260 330 420 350 C540 364 630 348 686 316 L686 393 L0 393 Z" fill="var(--band-grey)"/>
    <path d="M226 336 C330 352 400 366 470 378 L460 380 C390 370 320 356 226 336 Z" fill="var(--paper)"/>
    <path d="M0 373 C140 354 290 364 450 378 C560 386 640 374 686 348 L686 393 L0 393 Z" fill="var(--paper)"/>
    <path d="M0 380 C140 360 290 370 450 383 C560 391 640 380 686 354 L686 393 L0 393 Z" fill="var(--brand-green)"/>
  </svg>
</section>

<section class="card card--back" aria-label="Business card back">
  <span class="brand-mark" aria-hidden="true"></span>
  <div class="brand-name">Quillmark Homesteads</div>
  <div class="rule"></div>
  <p class="back-web">www.quillmarkhomesteads.co.nz</p>
</section>

</body>
</html>
```